Business Card Design Project

We are a construction company in Orange County, CA. We need a two sided business card. We would like the back to be our logo with web URL. Front should included Name, title, address, phone, fax and email address.

our address is
627 West Dorrance Blvd, Suite 308
Anaheim, CA 92718

Our logo files are attached.

Construction

```html
<!DOCTYPE html>
<html lang="en">
<head>
<meta charset="utf-8">
<title>Norvel Business Card</title>
<link rel="stylesheet" href="https://fonts.googleapis.com/css2?family=Arimo:wght@400;700&family=Tinos:wght@400&display=swap">
<style>
  :root {
    --bg: #eceef1;
    --card-white: #ffffff;
    --brand-blue: #22528a;
    --brand-navy: #1f4e85;
    --band-light: #5fb0dc;
    --accent-grey: #4a4d52;
    --text-dark: #1e1f22;
    --name-blue: #3a6ea5;
  }
  * { box-sizing: border-box; margin: 0; padding: 0; }
  html, body { width: 1200px; height: 900px; overflow: hidden; }
  body { background: var(--bg); position: relative; font-family: "Tinos", serif; }

  .card {
    position: absolute;
    width: 640px; height: 366px;
    border-radius: 20px;
    overflow: hidden;
    box-shadow: 0 10px 30px rgba(0,0,0,0.18);
  }

  /* Back side */
  .card-back { left: 80px; top: 60px; background: var(--brand-blue); }
  .card-back .brand-name {
    position: absolute; left: 0; right: 0; top: 128px;
    text-align: center;
    font-family: "Arimo", sans-serif; font-weight: 700;
    font-size: 92px; letter-spacing: -2px; color: var(--card-white);
    line-height: 1;
  }
  .card-back .web-url {
    position: absolute; right: 34px; bottom: 28px;
    font-size: 17px; color: var(--card-white);
  }

  /* Front side */
  .card-front { left: 480px; top: 474px; background: var(--card-white); }
  .card-front .side-band { position: absolute; left: 0; top: 0; width: 120px; height: 366px; }
  .card-front .brand-name {
    position: absolute; left: 168px; top: 28px;
    font-family: "Arimo", sans-serif; font-weight: 700;
    font-size: 60px; letter-spacing: -1px; color: var(--brand-navy);
    line-height: 1;
  }
  .address {
    position: absolute; left: 118px; top: 138px;
    font-size: 17px; line-height: 22px; color: var(--brand-navy);
  }
  .contact-list {
    position: absolute; left: 96px; top: 196px; list-style: none;
    font-size: 18px; color: var(--text-dark);
  }
  .contact-list li { display: flex; align-items: center; height: 24px; }
  .contact-list svg { width: 16px; height: 16px; margin-right: 18px; fill: var(--brand-navy); }
  .person { position: absolute; right: 34px; bottom: 40px; text-align: left; }
  .person-name { font-size: 23px; color: var(--name-blue); }
  .person-title { font-family: "Arimo", sans-serif; font-size: 17px; color: var(--text-dark); margin-top: 2px; }
</style>
</head>
<body>

<section class="card card-back">
  <div class="brand-name">NORVEL</div>
  <div class="web-url">www.norvelbuild.com</div>
</section>

<section class="card card-front">
  <svg class="side-band" viewBox="0 0 120 366" aria-hidden="true">
    <defs>
      <linearGradient id="band-fill" x1="0" y1="0" x2="0" y2="1">
        <stop offset="0" stop-color="#1f4e85"/>
        <stop offset="0.55" stop-color="#3f86c2"/>
        <stop offset="1" stop-color="#5fb0dc"/>
      </linearGradient>
    </defs>
    <path d="M0 0 H64 C44 110 30 250 0 330 Z" fill="url(#band-fill)"/>
    <path d="M70 0 C52 110 38 250 6 340" fill="none" stroke="var(--accent-grey)" stroke-width="5"/>
  </svg>

  <div class="brand-name">NORVEL</div>

  <address class="address" style="font-style:normal">
    627 West Dorrance Blvd, Suite 308<br>
    Anaheim, CA 92718
  </address>

  <ul class="contact-list">
    <li><svg viewBox="0 0 16 16"><path d="M2 5c0-2 2-3 6-3s6 1 6 3l-3 1-1-2H6L5 6zM4 8h8l2 6H2z"/></svg>(02) 8716 4420</li>
    <li><svg viewBox="0 0 16 16"><path d="M4 1h7v4H4zM2 6h12v9H2zm3 3v2h2V9zm4 0v2h2V9z"/></svg>(02) 8716 4428</li>
    <li><svg viewBox="0 0 16 16"><path d="M4 1h8v14H4zm2 2v8h4V3z"/></svg>0462 508 917</li>
    <li><svg viewBox="0 0 16 16"><path d="M1 3h14v10H1zm1 1 6 5 6-5z"/></svg>info@norvelbuild.com</li>
  </ul>

  <div class="person">
    <div class="person-name">Marcus D. Whitfield</div>
    <div class="person-title">General Manager</div>
  </div>
</section>

</body>
</html>
```